Looking for a modern, Professional business card design

We have a simple business card, but are looking for a more modern, professional look. A sample of the basic card is attached as well as the logo. We would also like to add that we offer:
Struggling with your finances?
- Learn to become debt free
- Discover the power of cash
- Control your money instead of it controlling you
Let us help you achieve a new level of financial freedom!
Also, we would like to have a "SPECIAL OFFER!: FREE 30 minute consultation"
Financial Planning

```html
<!DOCTYPE html>
<html lang="en">
<head>
<meta charset="utf-8">
<title>Clearpath Financial Coaching – Business Card</title>
<link rel="stylesheet" href="https://fonts.googleapis.com/css2?family=Open+Sans:ital,wght@0,400;0,600;0,700;0,800;1,400&display=swap">
<style>
  :root {
    --backdrop: #555657;
    --card-white: #ffffff;
    --green-light: #a9d23c;
    --green-mid: #6fb43a;
    --green-deep: #3e8b3b;
    --green-text: #3a9a3a;
    --ink: #1e1e1e;
    --ink-soft: #3a3a3a;
  }
  * { margin: 0; padding: 0; box-sizing: border-box; }
  html, body {
    width: 1105px;
    height: 1200px;
    overflow: hidden;
    background: var(--backdrop);
    font-family: "Open Sans", Arial, sans-serif;
  }
  .canvas {
    position: relative;
    width: 1105px;
    height: 1200px;
  }
  .card {
    position: absolute;
    left: 193px;
    width: 720px;
    height: 412px;
    overflow: hidden;
  }

  /* Front */
  .card-front {
    top: 181px;
    background: radial-gradient(ellipse 75% 95% at 42% 40%, var(--green-light) 0%, var(--green-mid) 45%, var(--green-deep) 100%);
    color: var(--card-white);
  }
  .card-front .edge-tab {
    position: absolute;
    right: 0;
    top: 190px;
    width: 16px;
    height: 50px;
    background: var(--card-white);
  }
  .identity {
    position: absolute;
    right: 40px;
    top: 182px;
    text-align: right;
  }
  .identity .name {
    font-size: 23px;
    font-weight: 600;
    letter-spacing: 0.3px;
    line-height: 1.2;
  }
  .identity .role {
    font-size: 18.5px;
    font-weight: 400;
    line-height: 1.3;
  }
  .contact {
    position: absolute;
    right: 40px;
    top: 280px;
    text-align: right;
    font-size: 18.5px;
    line-height: 27.5px;
  }
  .contact .label { font-weight: 700; }

  /* Back */
  .card-back {
    top: 637px;
    background: var(--card-white);
  }
  .offer {
    position: absolute;
    left: 58px;
    top: 61px;
    height: 292px;
    writing-mode: vertical-rl;
    transform: rotate(180deg);
    text-align: end;
  }
  .offer .headline {
    display: block;
    font-size: 25px;
    font-weight: 700;
    color: var(--green-text);
    line-height: 30px;
  }
  .offer .detail {
    display: block;
    font-size: 18.5px;
    font-weight: 600;
    color: var(--ink);
    line-height: 26px;
  }
  .brand {
    position: absolute;
    right: 40px;
    top: 62px;
    display: flex;
    align-items: center;
    gap: 14px;
  }
  .brand .mark {
    width: 34px;
    height: 34px;
    border-radius: 50%;
    background: var(--green-mid);
  }
  .brand .wordmark {
    font-size: 30px;
    font-weight: 800;
    color: var(--ink);
    line-height: 1.05;
    text-align: right;
  }
  .tagline {
    position: absolute;
    right: 40px;
    top: 175px;
    font-size: 10px;
    color: var(--ink-soft);
  }
  .pitch {
    position: absolute;
    right: 42px;
    top: 238px;
    text-align: right;
  }
  .pitch .question {
    font-size: 19px;
    font-weight: 700;
    color: var(--green-text);
    line-height: 26px;
    margin-bottom: 2px;
  }
  .benefits { list-style: none; }
  .benefits li {
    font-size: 18px;
    font-style: italic;
    color: var(--ink-soft);
    line-height: 26.5px;
  }
  .benefits li.point::after {
    content: "";
    display: inline-block;
    width: 9px;
    height: 9px;
    margin-left: 12px;
    border-radius: 50%;
    background: var(--green-text);
    vertical-align: middle;
  }
</style>
</head>
<body>
<main class="canvas">

  <section class="card card-front" aria-label="Business card front">
    <span class="edge-tab"></span>
    <div class="identity">
      <p class="name">DANIEL R. HAYES</p>
      <p class="role">PERSONAL FINANCIAL COACH</p>
    </div>
    <div class="contact">
      <p><span class="label">Mobile:</span> (205) 555-0187</p>
      <p>daniel@steadyledgercoach.com</p>
      <p>www.steadyledgercoach.com</p>
    </div>
  </section>

  <section class="card card-back" aria-label="Business card back">
    <div class="offer">
      <span class="headline">SPECIAL OFFER!</span>
      <span class="detail">FREE 30 minute consultation</span>
    </div>

    <div class="brand">
      <span class="mark"></span>
      <p class="wordmark">CLEARPATH<br>FINANCIAL COACHING</p>
    </div>
    <p class="tagline">Achieve a new level of personal freedom</p>

    <div class="pitch">
      <p class="question">STRUGGLING WITH YOUR FINANCES?</p>
      <ul class="benefits">
        <li class="point">Learn to become debt free</li>
        <li class="point">Discover the power of cash</li>
        <li class="point">Control your money instead of it controlling you</li>
        <li>Let us help you achieve a new level of financial freedom!</li>
      </ul>
    </div>
  </section>

</main>
</body>
</html>
```